Modern looking signage for dental office.

Exterior signage for passing cars
Updates
Need extra days to review
Target Market(s)
Cars passing by
Font styles to use
Sans Serif
Colors
3276b5
Requirements
Must have
- Logo
- OPEN ON SUTURDAY AND SUNDAY
- NIGHT CLINIC AVAILABLE
- PLEASE USE THE FONT TYPE IN FILE 4 UPLOADED BELOW.
- (847) 302-7469
- Modern looking

```html
<!DOCTYPE html>
<html lang="en">
<head>
<meta charset="utf-8">
<title>Peak Dental – Weekend &amp; Night Clinic Sign</title>
<link rel="stylesheet" href="https://fonts.googleapis.com/css2?family=Montserrat:wght@500;800;900&display=swap">
<style>
  :root {
    --page-bg: #d9d9d9;
    --sign-white: #ffffff;
    --sign-fade: #e9e9e9;
    --panel-black: #000000;
    --ink-dark: #3e3e40;
    --ink-mid: #4a4a4c;
    --rule-grey: #8a8a8a;
    --footer-grey: #dcdcdc;
    --icon-grey: #6b6b6b;
    --tooth-shade: #141414;
    --accent-blue: #3276b5;
  }
  * { margin: 0; padding: 0; box-sizing: border-box; }
  html, body {
    width: 1200px; height: 1000px; overflow: hidden;
    background: var(--page-bg);
    font-family: "Montserrat", Arial, sans-serif;
  }
  .sign {
    position: absolute; left: 192px; top: 92px;
    width: 816px; height: 816px;
    background: var(--sign-white);
    overflow: hidden;
  }
  .sign__header {
    position: absolute; left: 0; top: 0; width: 100%; height: 218px;
    background: linear-gradient(to bottom, var(--sign-white) 70%, var(--sign-fade));
  }
  .brand-mark {
    position: absolute; left: 78px; top: 43px;
    width: 140px; height: 140px; border-radius: 50%;
    border: 2px solid var(--ink-mid);
  }
  .brand-name {
    position: absolute; left: 234px; top: 72px;
    font-weight: 500; font-size: 78px; line-height: 1;
    letter-spacing: 1px; color: var(--ink-dark); white-space: nowrap;
  }
  .brand-tagline {
    position: absolute; left: 283px; top: 163px;
    font-weight: 500; font-size: 25px; line-height: 1;
    color: var(--ink-mid); white-space: nowrap;
  }
  .rule-bar {
    position: absolute; left: 0; width: 100%; height: 8px;
    background: var(--panel-black);
  }
  .rule-bar--top { top: 220px; }
  .rule-bar--bottom { top: 679px; }
  .message-panel {
    position: absolute; left: 0; top: 234px; width: 100%; height: 438px;
    background: var(--panel-black); color: var(--sign-white);
    text-align: center;
  }
  .tooth-decor {
    position: absolute; left: 0; top: 20px; width: 230px; height: 400px;
    background: var(--tooth-shade);
    border-radius: 40% 60% 30% 30%;
  }
  .message {
    position: absolute; left: 0; width: 100%;
    font-weight: 900; line-height: 1; white-space: nowrap;
  }
  .message--large { font-size: 94px; }
  .message--open { top: 58px; }
  .message--days { top: 150px; font-size: 50px; font-weight: 800; }
  .message--night { top: 252px; }
  .message--available { top: 346px; font-size: 70px; }
  .message-divider {
    position: absolute; left: 180px; top: 228px;
    width: 456px; height: 2px; background: var(--rule-grey);
  }
  .sign__footer {
    position: absolute; left: 0; top: 693px; width: 100%; height: 123px;
    background: var(--footer-grey);
  }
  .phone-icon {
    position: absolute; left: 104px; top: 26px; width: 70px; height: 70px;
  }
  .phone-number {
    position: absolute; left: 192px; top: 28px;
    font-weight: 800; font-size: 62px; line-height: 1;
    color: var(--panel-black); white-space: nowrap;
  }
</style>
</head>
<body>
  <div class="sign">
    <header class="sign__header">
      <div class="brand-mark"></div>
      <div class="brand-name">PEAK DENTAL</div>
      <div class="brand-tagline">MODERN GENERAL DENTISTRY</div>
    </header>

    <div class="rule-bar rule-bar--top"></div>

    <section class="message-panel">
      <div class="tooth-decor" role="img" aria-label="Faint tooth outline decoration"></div>
      <div class="message message--large message--open">OPEN ON</div>
      <div class="message message--days">SATURDAY AND SUNDAY</div>
      <div class="message-divider"></div>
      <div class="message message--large message--night">NIGHT CLINIC</div>
      <div class="message message--available">AVAILABLE</div>
    </section>

    <div class="rule-bar rule-bar--bottom"></div>

    <footer class="sign__footer">
      <svg class="phone-icon" viewBox="0 0 70 70" aria-hidden="true">
        <circle cx="35" cy="35" r="33" fill="var(--icon-grey)"/>
        <circle cx="35" cy="35" r="25" fill="var(--sign-white)"/>
        <path d="M24 20 l6 -2 l4 9 l-4 3 q3 7 10 10 l3 -4 l9 4 l-2 6 q-2 3 -6 3 q-13 -2 -21 -16 q-3 -7 1 -13z" fill="var(--icon-grey)"/>
        <path d="M38 22 a10 10 0 0 1 10 10 M38 16 a16 16 0 0 1 16 16" stroke="var(--icon-grey)" stroke-width="2.5" fill="none" stroke-linecap="round"/>
      </svg>
      <div class="phone-number">(847) 302-7469</div>
    </footer>
  </div>
</body>
</html>
```